Ductless Mini Split Business Website

Copper Fern Services is looking to design an eye catching educational website about installing Ductless mini splits.

Similar to this company.
https://www.halvikstream.com/

Coding

Coded - Design and coding required

```html
<!DOCTYPE html>
<html lang="en">
<head>
<meta charset="utf-8">
<title>Copper Fern Services – Ductless Mini Split Experts</title>
<link rel="stylesheet" href="https://fonts.googleapis.com/css2?family=Righteous&family=Montserrat:wght@300;400;500;600;700&display=swap">
<style>
:root{
  --yellow:#FFD800;
  --amber:#E8AC12;
  --amber-dark:#D99E0B;
  --ink:#141414;
  --text:#2a2a2a;
  --muted:#555;
  --white:#fff;
  --line:#cfcfcf;
}
*{box-sizing:border-box;margin:0;padding:0}
html,body{width:1200px;height:4873px;overflow:hidden}
body{position:relative;font-family:"Montserrat",sans-serif;color:var(--text);background:var(--white)}
.abs{position:absolute}
.display{font-family:"Righteous",sans-serif;color:var(--ink);text-transform:uppercase;letter-spacing:1px}
.hex{clip-path:polygon(50% 0,100% 25%,100% 75%,50% 100%,0 75%,0 25%)}
.btn-outline{display:flex;align-items:center;justify-content:center;border:2px solid var(--ink);font-weight:700;font-size:13px;color:var(--ink);text-transform:uppercase;background:var(--white)}
.btn-outline.clear{background:transparent}
.arrow{width:24px;height:24px;border:1.5px solid var(--ink);border-radius:50%;display:flex;align-items:center;justify-content:center}
.mascot{border-radius:50%;background:radial-gradient(circle at 45% 40%,#FFE24A 0 35%,#2b2b2b 36% 46%,#F4C20D 47% 62%,rgba(255,255,255,0) 63%)}
.brand{font-family:"Montserrat",sans-serif;font-weight:700;color:var(--amber-dark);display:flex;align-items:center;gap:10px}
.brand .dot{width:26px;height:26px;border-radius:50%;background:var(--yellow);flex:none}

/* header / hero */
.hero{left:0;top:0;width:1200px;height:644px;background:linear-gradient(120deg,#eef0f2 0%,#dfe3e6 40%,#c9d0d6 70%,#9aa6b0 100%)}
.hero-fade{left:0;top:0}
.topbar{right:0;top:0;width:510px;height:42px;background:var(--ink);clip-path:polygon(22px 0,100% 0,100% 100%,0 100%);color:var(--white);font-size:16px;display:flex;align-items:center;justify-content:flex-end;padding-right:157px;gap:6px}
.topbar b{color:var(--yellow);font-weight:600}
.nav{right:157px;top:58px;display:flex;gap:26px;font-size:14px;color:var(--ink)}
.logo{left:158px;top:34px;font-size:19px;flex-direction:column;align-items:flex-start;gap:4px}
.hero h1{left:161px;top:262px;font-size:47px;line-height:44px}
.hero p{left:161px;top:413px;width:300px;font-size:14px;line-height:19px;color:var(--ink)}

/* help */
.help-title{left:0;top:720px;width:1200px;text-align:center;font-size:44px;text-transform:none}
.service{width:208px;text-align:center}
.service .pic{width:170px;height:190px;margin:0 auto}
.service .tag{margin-top:12px;height:42px;background:var(--yellow);display:flex;align-items:center;justify-content:center;font-weight:700;font-size:15px;color:var(--ink)}

/* about */
.about-frame{left:0;top:1204px;width:580px;height:540px;border-top:6px solid var(--amber);border-right:6px solid var(--amber)}
.about-bg{left:587px;top:1243px;width:613px;height:499px;background:linear-gradient(135deg,var(--yellow),#F2C623)}
.eyebrow{left:157px;top:1294px;font-size:22px;font-weight:300;letter-spacing:1px;color:var(--ink)}
.about h2{left:157px;top:1324px;font-size:41px;line-height:41px}
.about p{left:157px;top:1458px;width:370px;font-size:13.5px;line-height:21px;color:var(--ink)}

/* call banner */
.callbar{left:151px;top:1954px;width:900px;height:76px;background:linear-gradient(100deg,var(--amber) 0 57%,var(--ink) 57%);display:flex;align-items:center;justify-content:space-between;padding:0 90px 0 17px}
.callbar p{font-size:15px;font-weight:600;line-height:20px;color:var(--ink);width:430px}
.callbar .num{font-size:22px;font-weight:600;color:var(--yellow);display:flex;align-items:center;gap:6px}

/* why */
.why h2{left:606px;top:2106px;font-size:40px;line-height:40px}
.why .lead{left:606px;top:2199px;width:390px;font-size:14.5px;line-height:23px;color:var(--ink)}
.feature{left:606px;width:450px;display:flex;gap:32px}
.feature .icon{width:104px;height:114px;background:var(--amber);display:flex;align-items:center;justify-content:center;flex:none;position:relative}
.feature .icon::before{content:"";position:absolute;inset:6px;background:var(--yellow);clip-path:inherit}
.feature .icon svg{position:relative}
.feature h3{font-size:19px;font-weight:700;color:var(--ink);margin-top:12px;line-height:24px}
.feature p{font-size:13px;line-height:19px;color:var(--muted);margin-top:8px;width:310px}

/* stand */
.stand h2{left:0;top:2806px;width:1200px;text-align:center;font-size:47px;line-height:49px}
.band{left:0;top:3214px;width:1200px;height:341px;background:var(--amber)}
.card-label{font-size:17px;font-weight:700;color:var(--ink);text-align:center;text-transform:uppercase}

/* contact */
.contact-photo{left:0;top:3555px;width:681px;height:515px;background:linear-gradient(135deg,#d8d2c6,#b9ad9a 55%,#7f7465)}
.contact h2{left:757px;top:3638px;font-size:40px;line-height:40px}
.field{left:757px;width:284px;height:34px;border:1px solid var(--line);font-size:11px;color:#777;padding:9px 12px}

/* testimonial */
.quote-box{left:151px;top:4070px;width:900px;height:341px;background:linear-gradient(135deg,var(--amber),#E5B52A);z-index:2}
.quote-box .stars{left:80px;top:70px;color:var(--white);font-size:16px;letter-spacing:3px}
.quote-box p{left:80px;top:104px;width:765px;font-size:13.5px;line-height:22px;color:var(--white)}

/* footer */
.footer{left:0;top:4363px;width:1200px;height:464px;background:#0c0c0c;color:var(--white)}
.footer h4{font-size:18px;font-weight:600}
.footer li{list-style:none;font-size:13px;line-height:31.5px}
.footer .info{font-size:13px;line-height:18px;display:flex;gap:14px;margin-bottom:14px}
.social{width:38px;height:38px;border-radius:50%;background:var(--yellow)}
.copy{left:0;top:4827px;width:1200px;height:46px;background:var(--amber);font-size:11px;color:var(--ink);display:flex;align-items:center;justify-content:center}
</style>
</head>
<body>

<!-- Hero -->
<section class="hero abs" role="img" aria-label="Photo of a technician servicing a wall-mounted ductless unit in a bright room">
  <svg class="hero-fade abs" width="1200" height="644" viewBox="0 0 1200 644"><polygon points="0,0 520,0 0,450" fill="#f7f7f7"/><polygon points="0,450 520,0 600,0 0,644" fill="#eceeef" opacity=".7"/></svg>
</section>
<div class="topbar abs">
  <svg width="12" height="16" viewBox="0 0 12 16"><rect x="1" y="1" width="10" height="14" rx="2" fill="none" stroke="#fff" stroke-width="1.5"/></svg>
  Call Us Toll Free: <b>+1 (555) 014 2323</b>
</div>
<nav class="nav abs"><span>About</span><span>Ductless Mini Split</span><span>Faq</span><span>Financing</span><span>Reviews</span><span>Contact</span></nav>
<div class="brand logo abs"><span style="display:flex;align-items:center;gap:10px"><span class="dot"></span>Copper Fern Services</span><span style="font-size:16px">Ductless Experts</span></div>
<div class="mascot abs" style="left:322px;top:150px;width:160px;height:135px" role="img" aria-label="Cartoon bee mascot holding tools"></div>
<h1 class="display abs" style="left:161px;top:262px;font-size:47px;line-height:44px">Ductless<br>Mini Split<br>Business</h1>
<p class="abs" style="left:161px;top:413px;width:300px;font-size:14px;line-height:19px;color:var(--ink)">Lorem ipsum dolor sit amet, consectetur adipiscing elit. Integer sed dapibusctus eget molestie felis.</p>
<div class="btn-outline abs" style="left:163px;top:487px;width:134px;height:36px;text-transform:none">Find Out More</div>
<div class="arrow abs" style="left:164px;top:551px"><svg width="8" height="10"><path d="M6 1 2 5l4 4" fill="none" stroke="#141414" stroke-width="1.5"/></svg></div>
<div class="arrow abs" style="left:196px;top:551px"><svg width="8" height="10"><path d="M2 1l4 4-4 4" fill="none" stroke="#141414" stroke-width="1.5"/></svg></div>

<!-- How can we help -->
<h2 class="display help-title abs">How Can We Help You?</h2>
<div class="service abs" style="left:157px;top:805px"><div class="pic hex" style="background:linear-gradient(135deg,#b8c3cc,#55606a)" role="img" aria-label="Technician replacing an outdoor unit"></div><div class="tag">REPLACEMENT</div></div>
<div class="service abs" style="left:383px;top:805px"><div class="pic hex" style="background:linear-gradient(135deg,#eceff1,#d28350)" role="img" aria-label="Technician remodelling an indoor wall unit"></div><div class="tag">REMODELS</div></div>
<div class="service abs" style="left:608px;top:805px"><div class="pic hex" style="background:linear-gradient(135deg,#e7eaec,#9aa3aa)" role="img" aria-label="Hands installing a split unit"></div><div class="tag">INSTALLATION</div></div>
<div class="service abs" style="left:833px;top:805px"><div class="pic hex" style="background:linear-gradient(135deg,#d9dcde,#7a746d)" role="img" aria-label="Technician maintaining an open air conditioner"></div><div class="tag">MAINTENANCE</div></div>
<div class="btn-outline abs" style="left:460px;top:1075px;width:282px;height:42px">More Copper Fern Services</div>

<!-- About -->
<div class="about-frame abs"></div>
<div class="about-bg abs"></div>
<div class="eyebrow abs">ABOUT US</div>
<h2 class="display abs" style="left:157px;top:1324px;font-size:41px;line-height:41px">Meet Our<br>CopperFern<br>Experts</h2>
<p class="abs" style="left:157px;top:1458px;width:370px;font-size:13.5px;line-height:21px;color:var(--ink)">Lorem ipsum dolor sit amet, consectetur adipiscing elit. Vivamus facilisis metus lacus, non posuere nulla porta eget. Duis sem ipsum, sollicitudin ac nisl ut, posuere molestie orci. In euismod lorem et orci auctor scelerisque. Curabitur euismod tortor quis magna gravida, nec suscipit turpis ultrices. Sed id condimentum tellus, sit amet facilisis purus. Nam non finibus velit.</p>
<div class="btn-outline abs" style="left:157px;top:1650px;width:135px;height:40px">Read More</div>
<div class="hex abs" style="left:590px;top:1293px;width:470px;height:492px;background:#fff"></div>
<div class="hex abs" style="left:596px;top:1300px;width:458px;height:478px;background:linear-gradient(135deg,#c7ccd1,#2a3a5c 60%,#1d2230)" role="img" aria-label="Technician cleaning the filter of an indoor unit"></div>
<div class="hex abs" style="left:876px;top:1189px;width:178px;height:202px;background:#fff"></div>
<div class="hex abs" style="left:881px;top:1195px;width:168px;height:190px;background:linear-gradient(135deg,#e8eaec,#4b5c7d)" role="img" aria-label="Technician working on a ceiling cassette unit"></div>
<div class="hex abs" style="left:587px;top:1660px;width:180px;height:205px;background:#fff"></div>
<div class="hex abs" style="left:592px;top:1666px;width:170px;height:193px;background:linear-gradient(135deg,#e9ebec,#a9b0b5)" role="img" aria-label="Technician fitting a wall unit"></div>

<!-- Call banner -->
<div class="mascot abs" style="left:148px;top:1770px;width:240px;height:190px" role="img" aria-label="Cartoon bee mascot with tools"></div>
<div class="callbar abs">
  <p>Call Copper Fern Services for all of your air conditioning and indoor air quality needs</p>
  <div class="num"><svg width="14" height="18" viewBox="0 0 14 18"><path d="M4 1C1 3 1 15 4 17l2-4-2-1c-.6-2-.6-4 0-6l2-1z" fill="#FFD800"/></svg>+1 (555) 014 2323</div>
</div>

<!-- Why choose -->
<svg class="abs" style="left:0;top:2054px" width="570" height="690" viewBox="0 0 570 690" role="img" aria-label="Worker in hard hat and safety vest mounting an indoor unit">
  <defs><linearGradient id="whyPhoto" x1="0" y1="0" x2="1" y2="1"><stop offset="0" stop-color="#f1f1f1"/><stop offset=".5" stop-color="#d9dcdf"/><stop offset="1" stop-color="#b8d64a"/></linearGradient></defs>
  <polygon points="0,0 562,178 364,690 0,690" fill="var(--amber)"/>
  <polygon points="0,14 548,184 352,690 0,690" fill="url(#whyPhoto)"/>
</svg>
<h2 class="display abs" style="left:606px;top:2106px;font-size:40px;line-height:40px">Why Choose<br>Copper Fern Services</h2>
<p class="abs" style="left:606px;top:2199px;width:390px;font-size:14.5px;line-height:23px;color:var(--ink)">Fusce maximus est mi. Cras sit amet odio turpis. Vestibulum ante ipsum primis in faucibus orci luctus et ultrices posuere cubilia Curae; Nulla ac eros in erat tincidunt</p>
<div class="feature abs" style="top:2324px"><div class="icon hex"><svg width="44" height="44" viewBox="0 0 44 44"><rect x="8" y="6" width="26" height="32" fill="none" stroke="#141414" stroke-width="3"/><path d="M14 14h14M14 21h14M14 28h8" stroke="#141414" stroke-width="3"/></svg></div><div><h3>0% Financing for 60 months</h3><p>Duis volutpat dignissim elit, at tincidunt justo auctor ut. Suspendisse ornarehendrerit nulla nec dapibus.</p></div></div>
<div class="feature abs" style="top:2457px"><div class="icon hex"><svg width="44" height="44" viewBox="0 0 44 44"><circle cx="22" cy="22" r="15" fill="none" stroke="#141414" stroke-width="3" stroke-dasharray="70 8"/><text x="22" y="29" text-anchor="middle" font-family="Montserrat,sans-serif" font-weight="700" font-size="19" fill="#141414">$</text></svg></div><div><h3>Money Back Guarantee</h3><p>Duis volutpat dignissim elit, at tincidunt justo auctor ut. Suspendisse ornarehendrerit nulla nec dapibus.</p></div></div>
<div class="feature abs" style="top:2590px"><div class="icon hex"><svg width="44" height="44" viewBox="0 0 44 44"><circle cx="22" cy="22" r="6" fill="#141414"/><path d="M11 40c0-8 5-11 11-11s11 3 11 11z" fill="#141414"/><path d="M22 4l1.5 3h3l-2.5 2 1 3-3-2-3 2 1-3-2.5-2h3zM10 9l1 2h2l-1.7 1.3.7 2-2-1.3-2 1.3.7-2L7 11h2zM34 9l1 2h2l-1.7 1.3.7 2-2-1.3-2 1.3.7-2L31 11h2z" fill="#141414"/></svg></div><div><h3>We Are the Experts in<br>Ductless Services</h3><p>Duis volutpat dignissim elit, at tincidunt justo auctor ut. Suspendisse ornarehendrerit nulla nec dapibus.</p></div></div>

<!-- Stand behind -->
<h2 class="display abs" style="left:0;top:2806px;width:1200px;text-align:center;font-size:47px;line-height:49px">We Stand Behind Our<br>Copper Fern Services</h2>
<div class="band abs"></div>
<div class="hex abs" style="left:159px;top:3023px;width:223px;height:258px;background:linear-gradient(135deg,#eef0f1,#2c2f33)" role="img" aria-label="Man adjusting a wall-mounted unit"></div>
<div class="hex abs" style="left:407px;top:2930px;width:384px;height:440px;background:linear-gradient(135deg,#e9e9e9,#c9c2b6 60%,#7a6e62)" role="img" aria-label="Hands reviewing financing charts on paper"></div>
<div class="hex abs" style="left:818px;top:3023px;width:223px;height:258px;background:linear-gradient(135deg,#f4f4f4,#d2d5d7)" role="img" aria-label="Close-up of an indoor split unit"></div>
<div class="mascot abs" style="left:880px;top:2887px;width:208px;height:170px" role="img" aria-label="Cartoon bee mascot waving"></div>
<div class="card-label abs" style="left:131px;top:3297px;width:280px">Get Some Answer</div>
<div class="btn-outline clear abs" style="left:204px;top:3335px;width:134px;height:38px">Our FAQ</div>
<div class="card-label abs" style="left:797px;top:3297px;width:280px">Stay Up To Date</div>
<div class="btn-outline clear abs" style="left:870px;top:3335px;width:134px;height:38px">Our Blog</div>
<div class="card-label abs" style="left:400px;top:3391px;width:400px;font-size:21px">Our Financing Options</div>
<div class="btn-outline clear abs" style="left:533px;top:3436px;width:134px;height:39px">Financing</div>

<!-- Contact -->
<div class="contact-photo abs" role="img" aria-label="Technician kneeling beside an outdoor condenser unit"></div>
<h2 class="display abs" style="left:757px;top:3638px;font-size:40px;line-height:40px">Contact Us<br>Today</h2>
<div class="field abs" style="top:3733px">Name:</div>
<div class="field abs" style="top:3778px">Email:</div>
<div class="field abs" style="top:3823px">Phone No:</div>
<div class="field abs" style="top:3868px;height:85px">Comments:</div>
<div class="btn-outline abs" style="left:757px;top:3966px;width:208px;height:40px">Send Information</div>

<!-- Footer -->
<footer class="footer abs">
  <div class="brand abs" style="left:157px;top:118px;font-size:20px;flex-direction:column;align-items:flex-start;gap:6px"><span style="display:flex;align-items:center;gap:10px"><span class="dot"></span>Copper Fern Services</span><span style="font-size:17px">Ductless Experts</span></div>
  <p class="abs" style="left:157px;top:243px;width:210px;font-size:12px;line-height:17px">Vestibulum ante ipsum primis in faucibus orci luctus et ultrices posuere cubilia Curae; Nulla ac eros in erat tincidunt</p>
  <div class="social abs" style="left:157px;top:345px" aria-label="Social link"></div>
  <div class="social abs" style="left:202px;top:345px" aria-label="Social link"></div>
  <div class="social abs" style="left:246px;top:345px" aria-label="Social link"></div>

  <div class="abs" style="left:432px;top:136px"><h4>Quick Links</h4>
    <ul style="margin-top:12px"><li>Home</li><li>About Us</li><li>FAQ</li><li>Financing</li><li>Contact Us</li><li>Privacy Policy</li><li>Site Map</li></ul></div>

  <div class="abs" style="left:608px;top:136px;width:200px"><h4 style="margin-bottom:22px">Contact Info</h4>
    <div class="info"><svg width="12" height="16" viewBox="0 0 12 16"><path d="M6 0a6 6 0 0 0-6 6c0 4 6 10 6 10s6-6 6-10a6 6 0 0 0-6-6z" fill="#FFD800"/><circle cx="6" cy="6" r="2" fill="#0c0c0c"/></svg><span>48, Larkspur Lane, 3rd Cross, Fernvale, USA 2040</span></div>
    <div class="info"><svg width="12" height="16" viewBox="0 0 14 18"><path d="M4 1C1 3 1 15 4 17l2-4-2-1c-.6-2-.6-4 0-6l2-1z" fill="#FFD800"/></svg><span>+1 (555) 014 2323</span></div>
    <div class="info"><svg width="12" height="16" viewBox="0 0 14 16"><rect x="1" y="4" width="12" height="8" fill="#FFD800"/><path d="M1 4l6 5 6-5" fill="none" stroke="#0c0c0c"/></svg><span style="font-size:12px">hello@copperfernservices.com</span></div>
    <div class="info"><svg width="12" height="16" viewBox="0 0 14 16"><circle cx="7" cy="8" r="6" fill="#FFD800"/><path d="M7 4v4l3 2" fill="none" stroke="#0c0c0c" stroke-width="1.5"/></svg><span>Mon - Sat: 09.00am<br>to 18.00pm</span></div>
  </div>

  <div class="abs" style="left:833px;top:136px;width:210px"><h4>Subscribe Today</h4>
    <p style="font-size:13px;line-height:19px;margin-top:14px">Subscribe us to get updates, news &amp; tips in your inbox.</p>
    <div style="margin-top:16px;height:30px;background:#fff;color:#888;font-size:11px;display:flex;align-items:center;padding-left:20px">Enter your mail id:</div>
    <div style="margin-top:8px;height:34px;background:var(--yellow);color:var(--ink);font-weight:700;font-size:15px;display:flex;align-items:center;justify-content:center">Subscribe Now</div>
  </div>
</footer>

<!-- Testimonial -->
<div class="abs" style="left:681px;top:4070px;width:370px;height:6px;background:var(--ink);z-index:3"></div>
<section class="quote-box abs">
  <svg class="abs" style="left:10px;top:84px" width="58" height="40" viewBox="0 0 58 40"><path d="M14 0C6 0 0 6 0 14s6 13 13 13c-1 6-5 10-10 12 12-2 23-10 24-24C27 6 21 0 14 0zM45 0c-8 0-14 6-14 14s6 13 13 13c-1 6-5 10-10 12 12-2 23-10 24-24C58 6 52 0 45 0z" fill="#141414"/></svg>
  <div class="stars abs">★★★★★</div>
  <p class="abs">Duis volutpat dignissim elit, at tincidunt justo auctor ut. Suspendisse ornare hendrerit nulla nec dapibus. Fusce magna felis, ultricies a tempor eu, interdum eget urna. Nullam pulvinar lacus sit amet sem maximus pulvinar. Vivamus lacinia condimentum sapien id scelerisque. Vestibulum pulvinar metus non magna congue, et convallis justo suscipit. <b style="color:var(--ink)">❞</b></p>
  <div class="abs" style="left:80px;top:210px;color:var(--ink);font-size:14px;font-weight:600">- Vestibulum Ante<div style="font-size:11px;font-weight:400;margin:2px 0 0 10px">Daucibus Orci</div></div>
  <div class="arrow abs" style="left:83px;top:268px"><svg width="8" height="10"><path d="M6 1 2 5l4 4" fill="none" stroke="#141414" stroke-width="1.5"/></svg></div>
  <div class="arrow abs" style="left:115px;top:268px"><svg width="8" height="10"><path d="M2 1l4 4-4 4" fill="none" stroke="#141414" stroke-width="1.5"/></svg></div>
</section>
<div class="mascot abs" style="left:946px;top:4240px;width:200px;height:171px;z-index:4" role="img" aria-label="Cartoon bee mascot with tools"></div>

<div class="copy abs">© 2019 Copper Fern Services. All rights reserved.</div>

</body>
</html>
```